Pitch Deck Powerpoint Template for Entrepreneurship/Education Based Nonprofit

I need a stylish powerpoint design for a start-up nonprofit called Harbor Venture Works (HVW). I am building HVWs pitch deck to raise money. HVW is an entrepreneurial incubator and accelerator that seeks to identify, validate, test, and launch innovative ventures that improve public education. An example of our model, and one of our partners, is Kestrel Schools in New Orleans and New York :http://kestrelsch.example.org

We need the deck to look sleek and innovative - like a start-up pitch deck. Lots of different templates and fonts that pop off the page.

Target Market(s)

Individuals, foundations, and any other stakeholder - we are pitching a new business model and asking for money.

Industry/Entity Type

Building

Font styles to use
Sans Serif

Requirements
Must have
• A sleek/modern feel with several different template slides. charts and graphs/ strong fonts that pop off the page, use of the logo:
• It would be great to have a slide describing the 3 primary programs at Harbor Venture Works (HVW):
• - HVWspark - come in with an idea for an innovation in education, and we will do a two day workshop to examine your business assumptions and discuss next steps.
• - HVWpropell - take your idea to a prototype and launch to customers - we help you with an intensive 30 day program
• - HVWnurture - for existing nonprofit projects, we allow you to work under our umbrella to launch and build capacity
• Slides: Problem Definition, Solution, Value Proposition, Data/MEasurement, Key Partners, About the founder, Key Advisors

```html
<!DOCTYPE html>
<html lang="en">
<head>
<meta charset="utf-8">
<title>Ask of Money – Harbor Venture Works</title>
<link rel="stylesheet" href="https://fonts.googleapis.com/css2?family=Oswald:wght@500&family=Open+Sans:wght@300;600;700;800&display=swap">
<style>
  :root {
    --stage: #000000;
    --paper: #ffffff;
    --navy: #0d4680;
    --magenta: #a8208c;
    --green: #5a9208;
    --red: #ed1c24;
    --ink: #111111;
    --grid: #333333;
    --page-num: #2a63c9;
  }
  * { margin: 0; padding: 0; box-sizing: border-box; }
  html, body { width: 1200px; height: 1200px; overflow: hidden; background: var(--stage); }
  .canvas { position: relative; width: 1200px; height: 1200px; background: var(--stage); font-family: "Open Sans", sans-serif; }
  .deck-heading {
    position: absolute; top: 83px; left: 0; width: 1200px; text-align: center;
    color: var(--paper); font-weight: 300; font-size: 32px; letter-spacing: 0.2px;
  }
  .slide { position: absolute; left: 42px; top: 181px; width: 1116px; height: 838px; background: var(--paper); overflow: hidden; }
  .title-bar {
    position: absolute; left: 0; top: 48px; width: 798px; height: 101px; background: var(--navy);
  }
  .title-bar h1 {
    position: absolute; left: 36px; top: 22px; color: var(--paper);
    font-family: "Oswald", sans-serif; font-weight: 500; font-size: 46px; line-height: 56px; letter-spacing: -0.3px;
    transform: scaleX(0.96); transform-origin: left center;
  }
  .brand { position: absolute; left: 829px; top: 52px; display: flex; align-items: flex-start; gap: 10px; }
  .brand-dot { width: 16px; height: 16px; border-radius: 50%; background: var(--magenta); margin-top: 10px; }
  .brand-name {
    color: var(--navy); font-weight: 800; font-size: 33px; line-height: 34px; letter-spacing: -0.5px;
  }
  .total-ask {
    position: absolute; left: 48px; top: 149px; display: flex; align-items: baseline; gap: 14px;
    font-family: "Oswald", sans-serif; font-weight: 500; transform: scaleX(0.86); transform-origin: left center;
  }
  .total-ask .label { color: var(--navy); font-size: 50px; letter-spacing: -0.5px; }
  .total-ask .amount { color: var(--magenta); font-size: 67px; letter-spacing: -1px; }
  .chart-card { position: absolute; top: 286px; width: 496px; height: 418px; border: 1.5px solid var(--navy); background: transparent; }
  .chart-card.growth { left: 47px; }
  .chart-card.financing { left: 577px; }
  .chart-card h2 {
    position: absolute; top: 16px; left: 0; width: 100%; text-align: center;
    font-weight: 700; font-size: 22px; color: var(--ink); letter-spacing: 0.3px;
  }
  .chart-card svg { position: absolute; left: 0; top: 0; }
  .axis-label { font-family: "Open Sans", sans-serif; font-size: 11.5px; font-weight: 600; fill: var(--ink); }
  .gridline { stroke: var(--grid); stroke-width: 1; stroke-dasharray: 4 3; }
  .axis { stroke: var(--grid); stroke-width: 1.5; }
  .bar-growth { fill: var(--green); }
  .bar-finance { fill: var(--red); }
  .footer {
    position: absolute; left: 0; top: 750px; width: 1116px; height: 88px;
    background: var(--magenta); border-top: 4px solid var(--navy);
  }
  .footer .page, .footer .site {
    position: absolute; top: 27px; color: var(--paper); font-weight: 700; font-size: 25px; line-height: 34px;
  }
  .footer .page { left: 48px; }
  .footer .site { right: 58px; }
  .sheet-number { position: absolute; right: 34px; bottom: 26px; color: var(--page-num); font-weight: 700; font-size: 13px; }
</style>
</head>
<body>
<div class="canvas">
  <div class="deck-heading">ASK OF MONEY</div>

  <section class="slide">
    <div class="title-bar"><h1>ASK OF MONEY</h1></div>

    <div class="brand">
      <span class="brand-dot"></span>
      <span class="brand-name">Harbor<br>Venture<br>Works</span>
    </div>

    <div class="total-ask"><span class="label">TOTAL ASK:</span><span class="amount">$100,000</span></div>

    <div class="chart-card growth">
      <h2>GROWTH OVER THE FIRST YEAR</h2>
      <svg width="496" height="418" viewBox="0 0 496 418">
        <g>
          <line class="gridline" x1="37" y1="88" x2="472" y2="88"/>
          <line class="gridline" x1="37" y1="137" x2="472" y2="137"/>
          <line class="gridline" x1="37" y1="186" x2="472" y2="186"/>
          <line class="gridline" x1="37" y1="235" x2="472" y2="235"/>
          <line class="gridline" x1="37" y1="284" x2="472" y2="284"/>
          <line class="gridline" x1="37" y1="333" x2="472" y2="333"/>
        </g>
        <g text-anchor="end">
          <text class="axis-label" x="29" y="89">60</text>
          <text class="axis-label" x="29" y="138">50</text>
          <text class="axis-label" x="29" y="187">40</text>
          <text class="axis-label" x="29" y="236">30</text>
          <text class="axis-label" x="29" y="285">20</text>
          <text class="axis-label" x="29" y="334">10</text>
          <text class="axis-label" x="25" y="385">0</text>
        </g>
        <g>
          <rect class="bar-growth" x="53.5" y="309" width="11" height="73"/>
          <rect class="bar-growth" x="94.5" y="261" width="11" height="121"/>
          <rect class="bar-growth" x="134.5" y="241" width="11" height="141"/>
          <rect class="bar-growth" x="175.5" y="226" width="11" height="156"/>
          <rect class="bar-growth" x="215.5" y="211" width="11" height="171"/>
          <rect class="bar-growth" x="257.5" y="187" width="11" height="195"/>
          <rect class="bar-growth" x="296.5" y="164" width="11" height="218"/>
          <rect class="bar-growth" x="336.5" y="150" width="11" height="232"/>
          <rect class="bar-growth" x="377.5" y="133" width="11" height="249"/>
          <rect class="bar-growth" x="418.5" y="110" width="11" height="272"/>
          <rect class="bar-growth" x="458.5" y="81" width="11" height="301"/>
        </g>
        <line class="axis" x1="37" y1="50" x2="37" y2="383"/>
        <line class="axis" x1="37" y1="382.5" x2="472" y2="382.5"/>
        <g text-anchor="middle">
          <text class="axis-label" x="59" y="400">JAN</text>
          <text class="axis-label" x="100" y="400">FEB</text>
          <text class="axis-label" x="140" y="400">MAR</text>
          <text class="axis-label" x="181" y="400">APR</text>
          <text class="axis-label" x="221" y="400">MAY</text>
          <text class="axis-label" x="263" y="400">JUN</text>
          <text class="axis-label" x="302" y="400">JUL</text>
          <text class="axis-label" x="342" y="400">SEP</text>
          <text class="axis-label" x="383" y="400">OCT</text>
          <text class="axis-label" x="424" y="400">NOV</text>
          <text class="axis-label" x="464" y="400">DEC</text>
        </g>
      </svg>
    </div>

    <div class="chart-card financing">
      <h2>STAGED FINANCING</h2>
      <svg width="496" height="418" viewBox="0 0 496 418">
        <g>
          <line class="gridline" x1="41" y1="88" x2="476" y2="88"/>
          <line class="gridline" x1="41" y1="137" x2="476" y2="137"/>
          <line class="gridline" x1="41" y1="186" x2="476" y2="186"/>
          <line class="gridline" x1="41" y1="235" x2="476" y2="235"/>
          <line class="gridline" x1="41" y1="284" x2="476" y2="284"/>
          <line class="gridline" x1="41" y1="333" x2="476" y2="333"/>
        </g>
        <g text-anchor="end">
          <text class="axis-label" x="37" y="89">60K</text>
          <text class="axis-label" x="37" y="138">50K</text>
          <text class="axis-label" x="37" y="187">40K</text>
          <text class="axis-label" x="37" y="236">30K</text>
          <text class="axis-label" x="37" y="285">20K</text>
          <text class="axis-label" x="37" y="334">10K</text>
          <text class="axis-label" x="30" y="385">0</text>
        </g>
        <g>
          <rect class="bar-finance" x="57.5" y="309" width="11" height="73"/>
          <rect class="bar-finance" x="98.5" y="261" width="11" height="121"/>
          <rect class="bar-finance" x="138.5" y="176" width="11" height="206"/>
          <rect class="bar-finance" x="179.5" y="226" width="11" height="156"/>
          <rect class="bar-finance" x="219.5" y="273" width="11" height="109"/>
          <rect class="bar-finance" x="261.5" y="187" width="11" height="195"/>
          <rect class="bar-finance" x="300.5" y="267" width="11" height="115"/>
          <rect class="bar-finance" x="340.5" y="150" width="11" height="232"/>
          <rect class="bar-finance" x="381.5" y="202" width="11" height="180"/>
          <rect class="bar-finance" x="421.5" y="245" width="11" height="137"/>
          <rect class="bar-finance" x="462.5" y="318" width="11" height="64"/>
        </g>
        <line class="axis" x1="41" y1="50" x2="41" y2="383"/>
        <line class="axis" x1="41" y1="382.5" x2="476" y2="382.5"/>
        <g text-anchor="middle">
          <text class="axis-label" x="63" y="400">JAN</text>
          <text class="axis-label" x="104" y="400">FEB</text>
          <text class="axis-label" x="144" y="400">MAR</text>
          <text class="axis-label" x="185" y="400">APR</text>
          <text class="axis-label" x="225" y="400">MAY</text>
          <text class="axis-label" x="267" y="400">JUN</text>
          <text class="axis-label" x="306" y="400">JUL</text>
          <text class="axis-label" x="346" y="400">SEP</text>
          <text class="axis-label" x="387" y="400">OCT</text>
          <text class="axis-label" x="427" y="400">NOV</text>
          <text class="axis-label" x="468" y="400">DEC</text>
        </g>
      </svg>
    </div>

    <footer class="footer">
      <span class="page">Page 1</span>
      <span class="site">www.hvw-example.org</span>
    </footer>
  </section>

  <div class="sheet-number">24</div>
</div>
</body>
</html>
```